Stonebrace Business Card Design

The Stonebrace Co is an aggregate (crushing) equipment dealer serving Western Canadian provinces. Stonebrace is a distributor of aggregate equipment for different manufacturers.

We are looking to change and update the existing business card which has been used since the existence of the company. A copy of existing card has been attached for reference. The Stonebrace Co logo we want to remain the same and we want the green color to remain the same.

We are wanting something new with a different look. A refreshing card to show a new modern and updated look. No longer wanting to have the manufacturers on the back of the card but something more like our logo on the back of the card with a statement like "Crushing Solutions"

ideas could be:
- card can be different colors on front and back
- front or reverse of the card could possibly be the green color with the logo in black

Target Market(s)

Owners of Aggregate/Crushing companies

Contact Information for Business Card

see above

Requirements
Must have
• - logo to remain same along with same font within logo
• - green color to remain same
Nice to have
• as noted above under project description
Should not have

```html
<!DOCTYPE html>
<html lang="en">
<head>
<meta charset="utf-8">
<title>Stonebrace Co – Business Card</title>
<link rel="stylesheet" href="https://fonts.googleapis.com/css2?family=Roboto+Condensed:wght@400;700&family=Roboto:wght@400;700&display=swap">
<style>
  :root {
    --backdrop: #2b2b2d;
    --card-dark: #1c1c1d;
    --card-light: #f3f3f2;
    --brand-green: #8a9317;
    --ink: #555556;
    --ink-soft: #c9c9c9;
    --white: #ffffff;
    --divider: #bdbdbd;
  }
  * { box-sizing: border-box; margin: 0; padding: 0; }
  html, body {
    width: 1200px; height: 900px; overflow: hidden;
    background: var(--backdrop);
  }
  .stage {
    width: 1200px; height: 900px;
    display: flex; flex-direction: column; align-items: center; justify-content: center;
    gap: 40px;
  }
  .card {
    width: 700px; height: 400px; position: relative;
    box-shadow: 0 10px 30px rgba(0,0,0,.45);
  }

  /* Back face */
  .card-back { background: var(--card-dark); color: var(--white); }
  .brand {
    position: absolute; top: 120px; left: 0; right: 0;
    display: flex; align-items: center; justify-content: center; gap: 22px;
  }
  .brand-dot { width: 58px; height: 58px; border-radius: 50%; background: var(--white); }
  .brand-name {
    font-family: "Roboto", Arial, sans-serif; font-weight: 700;
    font-size: 34px; letter-spacing: .5px; color: var(--white);
  }
  .tagline {
    position: absolute; top: 280px; left: 0; right: 0; text-align: center;
    font-family: "Roboto", Arial, sans-serif; font-weight: 700; font-size: 17px;
  }

  /* Front face */
  .card-front { background: var(--card-light); }
  .person {
    position: absolute; top: 128px; right: 386px; text-align: right;
  }
  .person-name {
    font-family: "Roboto Condensed", "Arial Narrow", sans-serif; font-weight: 700;
    font-size: 44px; line-height: 1; color: var(--brand-green);
  }
  .person-role {
    font-family: "Roboto Condensed", "Arial Narrow", sans-serif; font-weight: 400;
    font-size: 20px; letter-spacing: 1px; color: var(--ink-soft); margin-top: 2px;
  }
  .divider {
    position: absolute; left: 338px; top: 112px; width: 2px; height: 120px;
    background: linear-gradient(to bottom, transparent, var(--divider) 20%, var(--divider) 80%, transparent);
  }
  .contact-list {
    position: absolute; left: 362px; top: 116px; list-style: none;
    font-family: "Roboto", Arial, sans-serif; font-size: 19px; color: var(--ink);
  }
  .contact-list li { display: flex; align-items: center; gap: 12px; height: 23px; }
  .contact-list svg { width: 16px; height: 16px; fill: var(--brand-green); flex: none; }
  .address {
    position: absolute; left: 0; right: 0; top: 318px;
    display: flex; justify-content: center; align-items: center; gap: 10px;
    font-family: "Roboto", Arial, sans-serif; font-size: 19px; color: var(--ink);
  }
  .address svg { width: 16px; height: 22px; fill: var(--brand-green); }
</style>
</head>
<body>
<main class="stage">
  <section class="card card-back" aria-label="Card back">
    <div class="brand">
      <span class="brand-dot" aria-hidden="true"></span>
      <span class="brand-name">THE STONEBRACE CO.</span>
    </div>
    <p class="tagline">Crushing Solutions</p>
  </section>

  <section class="card card-front" aria-label="Card front">
    <div class="person">
      <p class="person-name">DALE HARTWICK</p>
      <p class="person-role">CEO/FOUNDER</p>
    </div>
    <div class="divider" aria-hidden="true"></div>
    <ul class="contact-list">
      <li>
        <svg viewBox="0 0 16 16" aria-hidden="true"><path d="M3.5 1l2.5 3-1.5 2c1 2 3 4 5 5l2-1.5 3 2.5-1.5 2.5C7 15 1 9 1 2.5z"/></svg>
        780.555.0142
      </li>
      <li>
        <svg viewBox="0 0 16 16" aria-hidden="true"><path d="M4 0h8a1 1 0 0 1 1 1v14a1 1 0 0 1-1 1H4a1 1 0 0 1-1-1V1a1 1 0 0 1 1-1zm1 2v10h6V2zm3 11a1 1 0 1 0 0 2 1 1 0 0 0 0-2z"/></svg>
        780.555.0187
      </li>
      <li>
        <svg viewBox="0 0 16 16" aria-hidden="true"><path d="M4 1h8v4H4zM1 6h14v7h-3v2H4v-2H1zm4 5v3h6v-3z"/></svg>
        780.555.0163
      </li>
      <li>
        <svg viewBox="0 0 16 16" aria-hidden="true"><path d="M1 3h14v10H1zm1.5 1.5L8 9l5.5-4.5z"/></svg>
        dale@stonebr.com
      </li>
      <li>
        <svg viewBox="0 0 16 16" aria-hidden="true"><circle cx="8" cy="8" r="7"/></svg>
        www.stonebrace.ca
      </li>
    </ul>
    <p class="address">
      <svg viewBox="0 0 16 22" aria-hidden="true"><path d="M8 0a8 8 0 0 1 8 8c0 6-8 14-8 14S0 14 0 8a8 8 0 0 1 8-8zm0 4.5a3.5 3.5 0 1 0 0 7 3.5 3.5 0 0 0 0-7z"/></svg>
      2210- 48B Avenue, Nisku, Alberta T9E 3K1
    </p>
  </section>
</main>
</body>
</html>
```